Design a New Business Card for Our Company

We are looking for fresh, unique, and a modern business card that reflects our roots as digital marketing agency focused on SEM.

Industry/Entity Type

Marketing

Contact Information for Business Card

looking for very unique out of the box designs. clean and modern that compliments our logo

Requirements
Must have
• colors should match our logo
• Front should have name, address, email, and phone/fax of the person, phone/fax are the same number
• back should have our url

```html
<!DOCTYPE html>
<html lang="en">
<head>
<meta charset="utf-8">
<title>Brightpath Media — Business Card</title>
<link rel="stylesheet" href="https://fonts.googleapis.com/css2?family=Open+Sans:wght@400;600;700&display=swap">
<style>
  :root {
    --backdrop: #2a2a2c;
    --brand-blue: #5596d1;
    --brand-grey: #a7a9ac;
    --ink: #2b2b2b;
    --muted: #9a9a9a;
    --rule: #cfcfcf;
    --paper: #ffffff;
  }
  * { box-sizing: border-box; margin: 0; padding: 0; }
  html, body {
    width: 1200px; height: 900px; overflow: hidden;
    background: var(--backdrop);
    font-family: "Open Sans", Arial, sans-serif;
  }
  .sheet { position: relative; width: 1200px; height: 900px; }
  .card {
    position: absolute; left: 250px; width: 700px; height: 400px;
    box-shadow: 0 10px 30px rgba(0,0,0,.45);
  }
  .brand { display: flex; align-items: center; gap: 18px; }
  .brand__dot { width: 46px; height: 46px; border-radius: 50%; background: currentColor; flex: none; }
  .brand__name { font-weight: 700; font-size: 50px; letter-spacing: -1px; line-height: 1; white-space: nowrap; }

  /* Back side */
  .card--back { top: 40px; background: var(--brand-blue); color: var(--paper); }
  .card--back .brand {
    position: absolute; left: 0; right: 0; top: 150px; justify-content: center;
  }
  .card--back .url {
    position: absolute; left: 0; right: 0; bottom: 36px;
    text-align: center; font-size: 16px; letter-spacing: .3px;
  }

  /* Front side */
  .card--front { top: 460px; background: var(--paper); color: var(--ink); }
  .front-header {
    position: absolute; left: 40px; right: 40px; top: 66px;
    display: flex; align-items: center; gap: 24px;
  }
  .card--front .brand { gap: 14px; color: var(--brand-blue); flex: none; }
  .card--front .brand__dot { width: 36px; height: 36px; }
  .card--front .brand__name { font-size: 36px; }
  .top-rule { flex: 1; border-top: 1px solid var(--rule); }
  .contacts {
    position: absolute; right: 40px; top: 120px;
    list-style: none; text-align: right; font-size: 16px; line-height: 26px;
  }
  .contacts li { display: flex; justify-content: flex-end; align-items: center; gap: 8px; }
  .contacts svg { width: 18px; height: 18px; flex: none; }
  .person { position: absolute; left: 40px; top: 232px; right: 40px; }
  .person__line { display: flex; align-items: center; gap: 14px; }
  .person__name { color: var(--brand-blue); font-weight: 700; font-size: 21px; white-space: nowrap; }
  .person__rule { flex: 1; border-top: 1px solid var(--rule); }
  .person__role { color: var(--muted); font-size: 15px; margin-top: 2px; }
  .address {
    position: absolute; left: 40px; bottom: 40px;
    font-style: normal; font-size: 17px; line-height: 25px;
  }
</style>
</head>
<body>
<main class="sheet">
  <section class="card card--back" aria-label="Card back">
    <div class="brand">
      <span class="brand__dot"></span>
      <span class="brand__name">Brightpath Media</span>
    </div>
    <p class="url">www.brightpathmedia.com</p>
  </section>

  <section class="card card--front" aria-label="Card front">
    <div class="front-header">
      <div class="brand">
        <span class="brand__dot"></span>
        <span class="brand__name">Brightpath Media</span>
      </div>
      <div class="top-rule"></div>
    </div>

    <ul class="contacts">
      <li>555.010.2040
        <svg viewBox="0 0 20 20" aria-hidden="true"><path fill="#5596d1" d="M3 7c0-2 2-3 7-3s7 1 7 3v1h-3V6.5H6V8H3zM5 9h10l1 7H4z"/></svg>
      </li>
      <li>555.010.2040
        <svg viewBox="0 0 20 20" aria-hidden="true"><path fill="#5596d1" d="M6 3h8v4H6zM3 8h14v7h-3v-3H6v3H3zM7 13h6v4H7z"/></svg>
      </li>
      <li>hello@brightpathmedia.com
        <svg viewBox="0 0 20 20" aria-hidden="true"><path fill="#5596d1" d="M2 5h16v10H2z"/><path fill="none" stroke="#fff" stroke-width="1.4" d="M2.5 5.5 10 11l7.5-5.5"/></svg>
      </li>
      <li>www.brightpathmedia.com
        <svg viewBox="0 0 20 20" aria-hidden="true"><g fill="none" stroke="#5596d1" stroke-width="1.4"><circle cx="10" cy="10" r="8"/><ellipse cx="10" cy="10" rx="3.5" ry="8"/><path d="M2 10h16M3.5 6h13M3.5 14h13"/></g></svg>
      </li>
    </ul>

    <div class="person">
      <div class="person__line">
        <span class="person__name">Dana Whitfield</span>
        <span class="person__rule"></span>
      </div>
      <p class="person__role">Owner</p>
    </div>

    <address class="address">N. 1 Harbor Lane, Suite 100,<br>Cedar Falls, WA 55555</address>
  </section>
</main>
</body>
</html>
```